KLW AUDITION

I need a post card design (front only) with this on it:
Bold Rising Steps (this is the main title to be in all caps)
Auditions
Date: Thursday June 30th
6:30-8:30 PM in person
Address: 4172 Fernwick BLVD, Oakland CA 94603
video submissions turn in by Sunday July 3rd, 2022 email:BoldRisingSteps22@tolvamail.com
Teens and Adults welcomed

SO PLEASE COME UP WITH A DESIGN THATS COLORFUL AND INVITING THX!

```html
<!DOCTYPE html>
<html lang="en">
<head>
<meta charset="utf-8">
<title>Bold Rising Steps – Auditions Postcard</title>
<link rel="stylesheet" href="https://fonts.googleapis.com/css2?family=League+Spartan:wght@300;700;800&family=Oswald:wght@500;600&family=Montserrat:wght@500;800&display=swap">
<style>
  :root{
    --page:#e4e2df;
    --night:#0d0a10;
    --violet:#3a1466;
    --magenta:#c0128f;
    --hot-pink:#e21cc4;
    --ribbon:#b5127f;
    --cyan:#56e3f4;
    --aqua:#6ff7f5;
    --mint:#1ff2b0;
    --white:#ffffff;
    --rule:#6b3b5c;
  }
  *{margin:0;padding:0;box-sizing:border-box}
  html,body{width:769px;height:1200px;overflow:hidden;background:var(--page)}
  .postcard{
    position:absolute;left:20px;top:357px;width:729px;height:486px;overflow:hidden;
    background:
      radial-gradient(ellipse 55% 45% at 62% 8%, #d21a9c 0%, rgba(210,26,156,0) 70%),
      radial-gradient(ellipse 45% 40% at 88% 30%, #a0127a 0%, rgba(160,18,122,0) 70%),
      radial-gradient(ellipse 50% 40% at 25% 45%, #2a1a6e 0%, rgba(42,26,110,0) 70%),
      linear-gradient(180deg, #7a0f6e 0%, var(--violet) 38%, #1c0b26 62%, var(--night) 78%);
    box-shadow:0 6px 18px rgba(0,0,0,.25);
    font-family:"League Spartan",sans-serif;color:var(--white);
  }
  .backdrop{position:absolute;inset:0}
  .dancers-photo{
    position:absolute;left:380px;top:60px;width:349px;height:420px;
    background:radial-gradient(ellipse 50% 50% at 55% 55%, rgba(196,30,140,.55) 0%, rgba(120,20,90,.25) 55%, rgba(0,0,0,0) 100%);
  }
  .title-top{
    position:absolute;left:60px;top:26px;font-weight:800;font-size:66px;line-height:1;letter-spacing:-1px;white-space:nowrap;
  }
  .title-top .accent{color:var(--cyan)}
  .title-main{position:absolute;left:56px;top:86px}
  .auditions{
    position:absolute;left:66px;top:254px;font-weight:800;font-size:42px;line-height:1;color:var(--cyan);letter-spacing:-1px;
  }
  .date-box{
    position:absolute;left:69px;top:299px;height:30px;display:flex;border:1.5px solid var(--mint);
    font-family:"Oswald",sans-serif;font-weight:500;font-size:21px;line-height:27px;
  }
  .date-box .day-month{background:var(--mint);color:#0b2a22;padding:0 6px}
  .date-box .day-month sup{font-size:11px;vertical-align:8px}
  .date-box .weekday{color:var(--mint);padding:0 10px}
  .time{position:absolute;left:71px;top:336px;font-weight:700;font-size:18px;letter-spacing:-.3px}
  .time small{font-size:13px}
  .submit-label{
    position:absolute;left:66px;top:384px;font-family:"Montserrat",sans-serif;font-weight:500;font-size:10.5px;letter-spacing:4.2px;
  }
  .details{position:absolute;left:66px;top:402px;width:276px;display:flex;align-items:center;gap:8px;padding-bottom:5px;border-bottom:1px solid var(--rule)}
  .deadline{color:var(--cyan);font-weight:700;font-size:13px;line-height:.95}
  .year{font-family:"Oswald",sans-serif;font-weight:500;font-size:26px;color:var(--mint);line-height:1;transform:scaleX(.78);transform-origin:left;margin-right:-9px;letter-spacing:.5px}
  .address{display:flex;align-items:center;gap:4px;font-weight:700;font-size:10.5px;line-height:.95;text-transform:uppercase}
  .email{position:absolute;left:66px;top:441px;display:flex;align-items:center;gap:7px;font-family:"Montserrat",sans-serif;font-size:11px;letter-spacing:1.3px}
  .welcome{
    position:absolute;left:472px;top:446px;font-family:"Montserrat",sans-serif;font-weight:800;font-size:9px;letter-spacing:1.6px;color:var(--hot-pink);text-transform:uppercase;
  }
</style>
</head>
<body>
<main class="postcard">
  <svg class="backdrop" width="729" height="486" viewBox="0 0 729 486" aria-hidden="true">
    <path d="M0,330 C110,350 230,385 330,372 C420,360 470,300 560,330 C640,355 690,330 729,345 L729,486 L0,486 Z" fill="#0d0a10"/>
    <path fill="var(--ribbon)" d="M0,175 C120,150 200,250 300,250 C420,250 470,222 560,250 C640,278 690,232 729,300 L729,440 C690,400 640,360 580,392 C500,432 470,330 400,340 C330,350 260,382 150,366 C80,356 30,332 0,320 Z"/>
    <path fill="#8e0d68" opacity=".6" d="M560,250 C640,278 690,232 729,300 L729,340 C690,300 650,300 600,320 C570,300 560,270 560,250 Z"/>
  </svg>

  <div class="dancers-photo" role="img" aria-label="Photo of two dancers: a ballerina in a pink leotard reaching upward and a street dancer in a cap and plaid shirt"></div>

  <h1 class="title-top">BOLD <span class="accent">RISING</span></h1>
  <svg class="title-main" width="600" height="130" viewBox="0 0 600 130" role="img" aria-label="STEPS">
    <defs>
      <linearGradient id="steps-fill" x1="0" y1="0" x2="0" y2="1">
        <stop offset="0" stop-color="#e21cf0"/>
        <stop offset=".5" stop-color="#9b7cf6"/>
        <stop offset=".8" stop-color="#6ff7f5"/>
      </linearGradient>
    </defs>
    <text x="0" y="120" font-family="League Spartan, sans-serif" font-weight="800" font-size="158" letter-spacing="2" textLength="580" lengthAdjust="spacingAndGlyphs" fill="url(#steps-fill)" stroke="#2ff2c8" stroke-width="2">STEPS</text>
  </svg>

  <h2 class="auditions">AUDITIONS</h2>
  <div class="date-box">
    <span class="day-month">30<sup>TH</sup> JUNE</span>
    <span class="weekday">THURSDAY</span>
  </div>
  <p class="time">6:30PM – 8:30PM <small>(IN PERSON)</small></p>

  <p class="submit-label">VIDEO SUBMISSIONS TURN IN BY</p>
  <div class="details">
    <span class="deadline">SUNDAY<br>JULY 3RD</span>
    <span class="year">2022</span>
    <span class="address">
      <svg width="13" height="17" viewBox="0 0 13 17" aria-hidden="true"><path d="M6.5 1a5.5 5.5 0 0 1 5.5 5.5c0 3.5-5.5 9-5.5 9S1 10 1 6.5A5.5 5.5 0 0 1 6.5 1z" fill="none" stroke="var(--hot-pink)" stroke-width="2"/><circle cx="6.5" cy="6.5" r="1.8" fill="var(--hot-pink)"/></svg>
      <span>4172 Fernwick BLVD,<br>Oakland CA 94603</span>
    </span>
  </div>
  <p class="email">
    <svg width="15" height="11" viewBox="0 0 15 11" aria-hidden="true"><rect width="15" height="11" fill="var(--hot-pink)"/><path d="M0 0 L7.5 6 L15 0" fill="none" stroke="#0d0a10" stroke-width="1.2"/></svg>
    BoldRisingSteps22@tolvamail.com
  </p>

  <p class="welcome">Teens and adults welcomed</p>
</main>
</body>
</html>
```